New business card/stationary for a consulting company

I am looking for a clean and very professional looking business card for my consulting company as well as corresponding stationary. I am uploading our logo. I like simple and powerful for the feel. No graphics but I am open on everything else. Below is my contact information but would like the final to be in a version I can add my employees information into and print. Thank you.

Daniel Whitcombe
dan@ferncliffadvisory.com
2870 North 9th Avenue, Summit Floor, Elm Ridge, Illinois 60531
www.ferncliffadvisory.com

Industry/Entity Type

Consulting

Contact Information for Business Card

Daniel Whitcombe
dan@ferncliffadvisory.com
www.ferncliffadvisory.com

Font styles to use
Serif
Sans Serif

Requirements
Must have
• Our logo and the business card details.
Nice to have
• our website www.ferncliffadvisory.com

```html
<!DOCTYPE html>
<html lang="en">
<head>
<meta charset="utf-8">
<title>Ferncliff Advisory – Business Card</title>
<link rel="stylesheet" href="https://fonts.googleapis.com/css2?family=Montserrat:wght@300;400&family=PT+Sans:wght@400;700&display=swap">
<style>
  :root {
    --page-bg: #e9e9ec;
    --royal-blue: #2424c4;
    --deep-blue: #0b0b72;
    --ink-navy: #1f1f7e;
    --paper: #f7f7f5;
    --text-grey: #5a5a5e;
    --white: #ffffff;
  }
  * { margin: 0; padding: 0; box-sizing: border-box; }
  html, body {
    width: 1200px;
    height: 900px;
    overflow: hidden;
    background: var(--page-bg);
  }
  .sheet {
    width: 1200px;
    height: 900px;
    display: flex;
    flex-direction: column;
    align-items: center;
    justify-content: center;
    gap: 50px;
  }
  .card {
    position: relative;
    width: 620px;
    height: 354px;
    box-shadow: 0 6px 18px rgba(0, 0, 0, 0.18);
  }
  .card--front {
    background: radial-gradient(ellipse at 20% 55%, var(--royal-blue) 0%, #1a1aa6 40%, var(--deep-blue) 100%);
  }
  .card--back {
    background: var(--paper);
  }
  .brand {
    position: absolute;
    left: 0;
    right: 0;
    display: flex;
    align-items: center;
    justify-content: center;
    gap: 14px;
  }
  .brand__square {
    width: 22px;
    height: 22px;
  }
  .brand__name {
    font-family: "Montserrat", sans-serif;
    font-weight: 300;
    font-size: 25px;
    letter-spacing: 0.06em;
    text-transform: uppercase;
    white-space: nowrap;
  }
  .card--front .brand { top: 128px; }
  .card--front .brand__square { background: var(--white); }
  .card--front .brand__name { color: var(--white); }
  .card--back .brand { top: 112px; }
  .card--back .brand__square { background: var(--ink-navy); }
  .card--back .brand__name { color: var(--ink-navy); }
  .front__web {
    position: absolute;
    left: 0;
    right: 0;
    bottom: 66px;
    text-align: center;
    font-family: "Montserrat", sans-serif;
    font-weight: 400;
    font-size: 13px;
    letter-spacing: 0.42em;
    color: var(--white);
  }
  .back__address {
    position: absolute;
    right: 40px;
    top: 142px;
    text-align: right;
    font-family: "PT Sans", sans-serif;
    font-size: 13px;
    line-height: 1.35;
    color: var(--text-grey);
  }
  .back__contact {
    position: absolute;
    left: 40px;
    bottom: 38px;
    font-family: "PT Sans", sans-serif;
    color: var(--text-grey);
    font-size: 14px;
    line-height: 1.3;
  }
  .back__name {
    font-weight: 700;
    font-size: 17px;
    color: var(--ink-navy);
    text-transform: uppercase;
    letter-spacing: 0.01em;
    margin-bottom: 2px;
  }
</style>
</head>
<body>
  <main class="sheet">
    <section class="card card--front" aria-label="Business card front">
      <div class="brand">
        <span class="brand__square"></span>
        <span class="brand__name">Ferncliff Advisory</span>
      </div>
      <p class="front__web">www.ferncliffadvisory.com</p>
    </section>

    <section class="card card--back" aria-label="Business card back">
      <div class="brand">
        <span class="brand__square"></span>
        <span class="brand__name">Ferncliff Advisory</span>
      </div>
      <address class="back__address" style="font-style: normal;">
        2870 North 9th Avenue<br>
        Summit Floor, Elm Ridge<br>
        Illinois 60531
      </address>
      <div class="back__contact">
        <p class="back__name">Daniel Whitcombe</p>
        <p class="back__email">dan@ferncliffadvisory.com</p>
        <p class="back__web">www.ferncliffadvisory.com</p>
      </div>
    </section>
  </main>
</body>
</html>
```